Corvane Capital Business Cards

These are professional business cards that are for my family office.
Put fake emails and phone numbers as of now until I finalize those components. This family office controls my families investments, assets, and future. The cards should be professional.
..
.
.
.
I just uploaded another variation of a logo I would like to see as a business card to I am inbeteen which logo to use

Target Market(s)

business

Industry/Entity Type

business

Contact Information for Business Card

Professional, wealth related, finance related.

Requirements
Must have
• Logo

```html
<!DOCTYPE html>
<html lang="en">
<head>
<meta charset="utf-8">
<title>Corvane Capital Business Cards</title>
<link href="https://fonts.googleapis.com/css2?family=Cinzel:wght@500;600&family=Arimo:wght@400&display=swap" rel="stylesheet">
<style>
  :root {
    --backdrop: #3a3a3a;
    --card-dark: #2e2e2e;
    --card-light: #ffffff;
    --ink-light: #f2f2f2;
    --ink-muted: #c8c8c8;
    --ink-navy: #1c2230;
    --emboss: #4a4a4a;
    --emboss-edge: #5a5a5a;
  }
  * { box-sizing: border-box; margin: 0; padding: 0; }
  html, body {
    width: 1200px; height: 803px; overflow: hidden;
    background: var(--backdrop);
  }
  .canvas {
    position: relative; width: 1200px; height: 803px;
  }
  .card {
    position: absolute; top: 262px;
    width: 500px; height: 280px;
    border-radius: 22px;
    box-shadow: 0 10px 28px rgba(0,0,0,.35);
    overflow: hidden;
  }
  .card--back { left: 70px; background: var(--card-dark); }
  .card--front { left: 630px; background: var(--card-light); }

  .back-emblem {
    position: absolute; right: 34px; top: 30px;
    width: 210px; height: 210px;
  }
  .back-details {
    position: absolute; left: 40px; bottom: 34px;
    color: var(--ink-light);
    font-family: "Arimo", Arial, sans-serif;
  }
  .firm-name {
    font-family: "Cinzel", "Times New Roman", serif;
    font-weight: 500; letter-spacing: 1px;
    font-size: 24px; color: var(--ink-light);
    margin-bottom: 26px;
  }
  .person-name {
    font-family: "Cinzel", "Times New Roman", serif;
    font-weight: 600; font-size: 19px; letter-spacing: .5px;
  }
  .person-role { font-size: 11px; color: var(--ink-muted); margin-bottom: 12px; }
  .address { font-size: 12px; line-height: 1.3; margin-bottom: 10px; }
  .contact-list { list-style: none; font-size: 12px; line-height: 1.4; }
  .contact-list li { display: flex; align-items: center; gap: 8px; }
  .contact-list svg { width: 10px; height: 10px; flex: none; }

  .front-brand {
    position: absolute; inset: 0;
    display: flex; flex-direction: column; align-items: center; justify-content: center;
    gap: 22px;
  }
  .brand-dot {
    width: 96px; height: 96px; border-radius: 50%;
    border: 3px solid var(--ink-navy);
  }
  .front-name {
    font-family: "Cinzel", "Times New Roman", serif;
    font-weight: 500; font-size: 30px; letter-spacing: 1.5px;
    color: var(--ink-navy);
  }
</style>
</head>
<body>
<main class="canvas">
  <section class="card card--back" aria-label="Card back with contact details">
    <svg class="back-emblem" viewBox="0 0 210 210" aria-hidden="true">
      <circle cx="105" cy="105" r="100" fill="none" stroke="var(--emboss-edge)" stroke-width="3"/>
    </svg>
    <div class="back-details">
      <p class="firm-name">Corvane Capital</p>
      <p class="person-name">Elias Marrow</p>
      <p class="person-role">President</p>
      <p class="address">412 Alder Row<br>Halvern, Canada 20817</p>
      <ul class="contact-list">
        <li><svg viewBox="0 0 10 10"><path d="M2 0.5 L4 2.8 L3 4 Q4.5 6 6 7 L7.2 6 L9.5 8 L8 9.5 Q3 9 0.5 2 Z" fill="currentColor"/></svg>555-210-4418</li>
        <li><svg viewBox="0 0 10 10"><rect x="2" y="0.5" width="6" height="9" rx="1" fill="none" stroke="currentColor"/></svg>555-210-7702</li>
        <li><svg viewBox="0 0 10 10"><rect x="0.5" y="2" width="9" height="6.5" fill="none" stroke="currentColor"/><path d="M0.5 2 L5 6 L9.5 2" fill="none" stroke="currentColor"/></svg>info@corvanecapital.com</li>
        <li><svg viewBox="0 0 10 10"><circle cx="5" cy="5" r="4.5" fill="none" stroke="currentColor"/><path d="M0.5 5 H9.5 M5 0.5 Q2 5 5 9.5 Q8 5 5 0.5" fill="none" stroke="currentColor" stroke-width=".8"/></svg>www.corvanecapital.com</li>
      </ul>
    </div>
  </section>

  <section class="card card--front" aria-label="Card front with firm name">
    <div class="front-brand">
      <div class="brand-dot"></div>
      <p class="front-name">Corvane Capital</p>
    </div>
  </section>
</main>
</body>
</html>
```